Make a great menu for our Seafood Restaurant MarLo

Design a iconic menu for my fish restaurant on the island of Phu Quoc, Vietnam. Coastal, seafood and pictures of all menu items inside. For our restaurant menu help us transform our food photos and some saucy sentences into a complete, professional restaurant menu.

A logo is in the works, leave empty space, colors will be mostly blue on lots of white, not all dishes have to be in the menu but most should be in there.

Should be a classy menu, not to busy looking.

Ive attached two samples. Attached also all images.

Target Market(s)

Mostly Asian guests

Industry/Entity Type

Seafood Restaurant

Font styles to use
Sans Serif
Decorative
Script

Colors
3176b5
33a6d7
0692cd
0255a3
85abd2
85cae6
ecf7fb
cfdeed
ffffff

Requirements
Must have
• Sazz, lots of pictures, cool menu, playfull and cheeky, but still classy if this makes any sense.
• Size of menu probably half A3, like 25CM wide by 36 CM high

```html
<!DOCTYPE html>
<html lang="en">
<head>
<meta charset="utf-8">
<title>MarLo Seafood Menu</title>
<link rel="stylesheet" href="https://fonts.googleapis.com/css2?family=Great+Vibes&family=Montserrat:wght@400;500;600&display=swap">
<style>
  :root {
    --blue-deep: #0255a3;
    --blue-mid: #3176b5;
    --blue-bright: #0692cd;
    --blue-sky: #33a6d7;
    --blue-soft: #85cae6;
    --blue-mist: #85abd2;
    --blue-pale: #cfdeed;
    --blue-ice: #ecf7fb;
    --white: #ffffff;
    --ink: #3a4149;
    --ink-soft: #6a737c;
  }
  * { margin: 0; padding: 0; box-sizing: border-box; }
  html, body { width: 835px; height: 1200px; overflow: hidden; background: var(--white); }
  .menu {
    position: relative; width: 835px; height: 1200px; overflow: hidden;
    background: var(--white);
    font-family: "Montserrat", sans-serif; color: var(--ink);
  }
  .wash { position: absolute; border-radius: 50%; filter: blur(28px); }
  .wash--top { left: -120px; top: -170px; width: 1080px; height: 500px;
    background: radial-gradient(ellipse at 50% 45%, var(--blue-soft) 0%, var(--blue-ice) 55%, rgba(255,255,255,0) 75%); }
  .wash--right { right: -140px; top: 300px; width: 420px; height: 620px;
    background: radial-gradient(ellipse at 60% 50%, var(--blue-pale) 0%, rgba(236,247,251,0.6) 50%, rgba(255,255,255,0) 75%); }
  .wash--left { left: -180px; top: 600px; width: 420px; height: 520px;
    background: radial-gradient(ellipse at 40% 50%, var(--blue-ice) 0%, rgba(255,255,255,0) 70%); }
  .wash--bottom { left: 120px; bottom: -220px; width: 720px; height: 340px;
    background: radial-gradient(ellipse at 50% 40%, var(--blue-pale) 0%, var(--blue-ice) 45%, rgba(255,255,255,0) 75%); }

  .section-title {
    position: absolute; left: 0; width: 100%; text-align: center;
    font-family: "Great Vibes", cursive; font-weight: 400;
    color: var(--blue-sky); font-size: 68px; line-height: 1;
    text-shadow: 0 0 2px var(--white), 0 0 6px var(--white);
  }
  .section-title--starter { top: 30px; }
  .section-title--main { top: 305px; font-size: 78px; }

  .starters { position: absolute; top: 148px; left: 22px; width: 790px;
    display: grid; grid-template-columns: repeat(5, 1fr); gap: 12px; }
  .starter__photo { height: 72px; border-radius: 40px / 30px; margin: 0 6px;
    background: radial-gradient(ellipse at 50% 50%, #c9a27a 0%, #e8ddd0 45%, #f6f3ef 70%);
    box-shadow: 0 4px 10px rgba(2,85,163,0.12); }
  .starter__name { margin-top: 12px; font-size: 8.5px; font-weight: 600; letter-spacing: 0.6px;
    color: var(--blue-bright); text-transform: uppercase; line-height: 1.3; }
  .starter__desc { margin-top: 3px; font-size: 7.5px; color: var(--ink-soft); line-height: 1.35; }

  .dish { position: absolute; width: 330px; }
  .dish__photo { border-radius: 50%; box-shadow: 0 8px 18px rgba(2,85,163,0.14); }
  .dish__name { font-size: 18px; font-weight: 600; letter-spacing: 0.6px; color: var(--blue-bright);
    text-transform: uppercase; line-height: 1.2; }
  .dish__tag { font-size: 11px; font-weight: 500; color: var(--blue-mist); letter-spacing: 0; }
  .dish__desc { margin-top: 5px; font-size: 14px; color: var(--ink); line-height: 1.3; }

  .photo-tuna { position: absolute; left: 60px; top: 398px; width: 240px; height: 145px;
    background: radial-gradient(ellipse at 50% 45%, #b98062 0%, #d9c2b2 35%, #eceae6 60%, #f7f7f5 80%); }
  .photo-coconut { position: absolute; left: 555px; top: 372px; width: 185px; height: 178px;
    background: radial-gradient(ellipse at 50% 35%, #f2efe4 0%, #d9d2a8 45%, #8aa25a 70%, #6c8a3e 85%); }
  .photo-seabass { position: absolute; left: 90px; top: 662px; width: 210px; height: 128px;
    background: radial-gradient(ellipse at 50% 50%, #c9a36a 0%, #d8c6a6 40%, #ece8e0 70%); }
  .photo-prawns { position: absolute; left: 530px; top: 704px; width: 210px; height: 110px;
    background: radial-gradient(ellipse at 50% 50%, #d8743e 0%, #e6b08a 40%, #efe9e2 70%); }
  .photo-oysters { position: absolute; left: 60px; top: 888px; width: 250px; height: 145px;
    background: radial-gradient(ellipse at 50% 50%, #e5c46a 0%, #e9dcb5 40%, #f2efe8 70%); }
  .photo-lobster { position: absolute; left: 500px; top: 884px; width: 260px; height: 150px;
    background: radial-gradient(ellipse at 50% 50%, #d0532f 0%, #dfa283 38%, #ede6e0 70%); }

  .dish--tuna { left: 62px; top: 566px; }
  .dish--squid { left: 505px; top: 566px; width: 310px; }
  .dish--seabass { left: 62px; top: 830px; }
  .dish--prawns { left: 505px; top: 830px; width: 310px; }
  .dish--oysters { left: 62px; top: 1050px; width: 350px; }
  .dish--lobster { left: 505px; top: 1050px; width: 310px; }
</style>
</head>
<body>
<main class="menu">
  <div class="wash wash--top" aria-hidden="true"></div>
  <div class="wash wash--right" aria-hidden="true"></div>
  <div class="wash wash--left" aria-hidden="true"></div>
  <div class="wash wash--bottom" aria-hidden="true"></div>

  <h1 class="section-title section-title--starter">Starter</h1>

  <section class="starters">
    <article class="starter">
      <div class="starter__photo" role="img" aria-label="Photo of grilled octopus skewers on a plate"></div>
      <h3 class="starter__name">Grilled Octopus Skewers</h3>
      <p class="starter__desc">Lemongrass glaze, Phu Quoc black pepper, fresh herbs</p>
    </article>
    <article class="starter">
      <div class="starter__photo" role="img" aria-label="Photo of caramelized prawns in a bowl"></div>
      <h3 class="starter__name">Roasted Mini Caramelized Prawns</h3>
      <p class="starter__desc">Roasted in coconut sugar, garlic and chili, house dip</p>
    </article>
    <article class="starter">
      <div class="starter__photo" role="img" aria-label="Photo of spring rolls with dipping sauce"></div>
      <h3 class="starter__name">Chef's Crab Spring Rolls</h3>
      <p class="starter__desc">Crisp rolls filled with crab, glass noodles, herbs, sweet chili</p>
    </article>
    <article class="starter">
      <div class="starter__photo" role="img" aria-label="Photo of fish ceviche in a glass"></div>
      <h3 class="starter__name">Phu Quoc Ceviche</h3>
      <p class="starter__desc">Fresh fish, lime, avocado, red onion, crisp shallots</p>
    </article>
    <article class="starter">
      <div class="starter__photo" role="img" aria-label="Photo of fresh oysters on ice"></div>
      <h3 class="starter__name">Chef's Natural Bed Oysters</h3>
      <p class="starter__desc">Six local oysters, lime, shallot vinegar, chili salt</p>
    </article>
  </section>

  <h2 class="section-title section-title--main">Main</h2>

  <div class="dish__photo photo-tuna" role="img" aria-label="Photo of grilled rose tuna with scallop and beetroot"></div>
  <div class="dish__photo photo-coconut" role="img" aria-label="Photo of squid salad served in a coconut"></div>
  <div class="dish__photo photo-seabass" role="img" aria-label="Photo of steamed sea bass in a bowl"></div>
  <div class="dish__photo photo-prawns" role="img" aria-label="Photo of grilled prawns with risotto"></div>
  <div class="dish__photo photo-oysters" role="img" aria-label="Photo of baked oysters with crispy oyster crepes"></div>
  <div class="dish__photo photo-lobster" role="img" aria-label="Photo of grilled rock lobster with salad"></div>

  <article class="dish dish--tuna">
    <h3 class="dish__name">Grilled Rose Tuna <span class="dish__tag">GF</span></h3>
    <p class="dish__desc">Grilled, scallop, beetroot, grapefruit, cress<br>GF</p>
  </article>
  <article class="dish dish--squid">
    <h3 class="dish__name">Poached Squid<br>Bathing in a Coconut</h3>
    <p class="dish__desc">Warm served poached Squid salad, lime, chilly, red onion, Vietnamese basil, mint, iceberg salad<br>GF</p>
  </article>
  <article class="dish dish--seabass">
    <h3 class="dish__name">Steamed Sea Bass <span class="dish__tag">(GF)</span></h3>
    <p class="dish__desc">With lemon grass, chilly, and lime</p>
  </article>
  <article class="dish dish--prawns">
    <h3 class="dish__name">Grilled Prawns <span class="dish__tag">(GF)</span></h3>
    <p class="dish__desc">With fresh coconut Risotto risotto, cilantro</p>
  </article>
  <article class="dish dish--oysters">
    <h3 class="dish__name">Chef's Signature Oysters <span class="dish__tag">(GF)</span></h3>
    <p class="dish__desc">French savory crepes, crispy oysters, spinach, traditional beurre blanc sauce</p>
  </article>
  <article class="dish dish--lobster">
    <h3 class="dish__name">Tomo's Rock Lobster <span class="dish__tag">(GF)</span></h3>
    <p class="dish__desc">Sweet apple, sour yoghurt, bitter melon, salted lemon, mint<br>GF</p>
  </article>
</main>
</body>
</html>
```